Website Redesign for Non-Profit Ministry & Church

NOTE: Please do not contact me privately — all private inquiries will be ignored.

Individuals seeking spiritual healing, community connection, ministry support and journal-based encounters.

Description of What’s Needed

We need a clean, fresh, inviting website that encourages engagement and connection. The site should feel warm and accessible, draw people in, and clearly present who we are, what we offer, and how visitors can participate. The layout should be straightforward, with well-structured pages (no overlapping objects, minimal layering complexity) and easy to navigate. Use only Google Fonts. All stock photos must be sourced from royalty-free sites and include proper attribution. We will not include a search feature.

Pages to Create
1. Home Page – impactful hero area, clear call-to-action, visual story of ministry, giving/gathering invitation.
2. About Us – vision, mission, leadership, testimonies, history.
3. Meetings & Events – upcoming gatherings, schedule, how to attend, sign-up or interest form.
4. Encounter: “Lanterns by the River” (book) – dedicated page for the book, overview, purchase link or details, journal prompts, imagery.
5. Healing Rooms / Ministry – explain ministry offerings, invite participation, testimonials or case-studies.
6. Live Stream & Links Page – page listing links for YouTube live stream, other platforms, archive links; simple layout.

Colour & Branding

Use colours that blend with our existing logo (attached). The palette should feel contemporary, welcoming, and aligned with ministry themes of restoration, healing and love. Ensure text, button and link colours maintain good contrast for accessibility.

Existing Content & Reference

Please gather available content from our current website in the attachment here for text, images and structure for reuse.

Imagery Guidelines

– Use original photos from our Facebook page or Google Location listing for building or people images when available.
– If generic images are used, ensure they depict appropriate ministry-related buildings or people (community, warm gathering) — avoid generic unrelated stock imagery.
– All photos must be royalty-free or have proper licensing and attribution.
– No overlapping objects or visual clutter; clean layouts with defined sections.

Additional Notes

– Integration: We currently utilise MailChimp for email communication; the design should include a connection/invite to subscribe (via MailChimp) but no blog page is required at this time.
– Payment/Giving: We accept PayPal and already have a giving portal; include clear donation/give buttons or calls-to-action linking to existing giving systems.
– No search function to be included.
– Layouts should avoid complex layering or overlapping elements—designers should work with distinct content blocks, clear visual hierarchy, and straightforward mobile-friendly structure.

Target Market(s)

Industry/Entity Type

Church/Religious institution

Number of Pages Required

5+ page

Requirements
Should not have
• search bar

```html
<!DOCTYPE html>
<html lang="en">
<head>
<meta charset="utf-8">
<title>Mended Loved Whole — Home</title>
<link href="https://fonts.googleapis.com/css2?family=Quicksand:wght@500;600;700&family=Nunito+Sans:wght@400;600;700&family=Open+Sans:wght@400;600;700&display=swap" rel="stylesheet">
<style>
:root{
  --teal:#0aa394;
  --teal-dark:#078a7d;
  --purple:#6a2c91;
  --green-bar:#17793a;
  --ink:#1d1d1d;
  --muted:#5f5f5f;
  --footer:#0b0b0b;
  --white:#ffffff;
}
*{box-sizing:border-box;margin:0;padding:0}
html,body{width:1200px;height:3782px;overflow:hidden}
body{position:relative;background:var(--white);font-family:"Nunito Sans",sans-serif;color:var(--ink)}
.abs{position:absolute}
a{color:inherit;text-decoration:none}

/* Header */
.topbar{left:415px;top:0;width:785px;height:48px;background:var(--green-bar);clip-path:polygon(28px 0,100% 0,100% 100%,0 100%);display:flex;align-items:center;justify-content:flex-end;gap:34px;padding-right:28px;color:var(--white);font-family:"Open Sans",sans-serif;font-size:13px;letter-spacing:.3px}
.topbar span{display:flex;align-items:center;gap:10px}
.topbar svg{width:20px;height:20px}
.brand{left:110px;top:20px;display:flex;align-items:center;gap:12px;font-family:"Quicksand",sans-serif;font-weight:700;font-size:26px;line-height:1;color:var(--teal);width:220px}
.brand-dot{width:22px;height:22px;border-radius:50%;background:var(--teal);flex:none}
.brand-name{display:block;width:150px;line-height:28px}
.nav{left:367px;top:64px;display:flex;align-items:center;gap:20px;font-size:12.5px;color:var(--ink)}
.nav a.active{background:var(--teal);color:var(--white);padding:8px 11px;border-radius:3px;font-weight:700}
.btn-contact{left:967px;top:59px;width:123px;height:39px;background:var(--purple);color:var(--white);border-radius:5px;font-family:"Open Sans",sans-serif;font-weight:700;font-size:14px;letter-spacing:1px;display:flex;align-items:center;justify-content:center}

/* Hero */
.hero{left:0;top:110px;width:1200px;height:640px;background:linear-gradient(180deg,#b9b7c6 0%,#6c6b78 35%,#3a3740 70%,#2a2a2e 100%)}
.hero-title{left:0;top:360px;width:1200px;text-align:center;font-family:"Quicksand",sans-serif;font-weight:700;font-size:74px;letter-spacing:6px;color:var(--white)}
.hero-sub{left:0;top:462px;width:1200px;text-align:center;font-family:"Open Sans",sans-serif;font-weight:700;font-size:17px;letter-spacing:2px;color:var(--white)}
.btn{background:var(--teal);color:var(--white);border-radius:5px;font-family:"Open Sans",sans-serif;font-weight:700;font-size:14px;letter-spacing:1.5px;display:flex;align-items:center;justify-content:center}
.hero-btn{left:555px;top:510px;width:90px;height:37px}
.hero-wave{left:0;top:640px;width:1200px;height:115px}

/* Who we are */
.who-photo{left:111px;top:815px;width:446px;height:394px;border-radius:4px;background:linear-gradient(135deg,#d9d3c8,#8a7f9c 55%,#3f3650)}
.section-title{font-family:"Quicksand",sans-serif;font-weight:600;font-size:40px;color:var(--ink);display:flex;align-items:center;gap:10px}
.section-title b{color:var(--purple);font-weight:700}
.mark{width:26px;height:26px;border-radius:50%;border:3px solid var(--teal);flex:none}
.who-title{left:640px;top:808px}
.who-text{left:641px;top:878px;width:445px;font-size:13.5px;line-height:28.5px;color:var(--muted)}
.who-text p{margin-bottom:5px}
.who-btn{left:641px;top:1157px;width:107px;height:41px}

/* Book band */
.book-band{left:0;top:1298px;width:1200px;height:502px;background:linear-gradient(90deg,#1f2330 0%,#363544 50%,#24263a 100%)}
.book-title{left:114px;top:1398px;font-family:"Quicksand",sans-serif;font-weight:700;font-size:43px;letter-spacing:4px;color:var(--white);display:flex;align-items:center;gap:16px}
.book-title .mark{border-color:var(--white);width:32px;height:32px}
.book-text{left:116px;top:1468px;width:480px;font-family:"Open Sans",sans-serif;font-size:15px;line-height:32.5px;letter-spacing:1.2px;color:var(--white)}
.book-btn{left:113px;top:1686px;width:96px;height:39px}
.book-cover{left:782px;top:1350px;width:250px;height:330px;background:linear-gradient(160deg,#1d4a36,#2e6e3e 55%,#b79a24);border:3px solid #d9d2b8;box-shadow:6px 6px 0 #ece6d2}

/* Blog */
.blog-title{left:0;top:1900px;width:1200px;justify-content:center}
.card{top:1995px;width:318px}
.card-img{width:318px;height:254px;border-radius:5px}
.card-cat{margin-top:18px;color:var(--teal);font-weight:700;font-size:15px}
.card-h{margin-top:14px;font-size:20px;line-height:30px;color:var(--ink);min-height:30px}
.card-meta{margin-top:20px;display:flex;gap:34px;font-size:13px;color:var(--muted)}
.card-meta span{display:flex;align-items:center;gap:8px}
.card-meta i{display:inline-block;width:16px;height:13px;border:1.5px solid #888;border-radius:2px}
.arrow{top:2118px;width:20px;height:20px;border-radius:50%;display:flex;align-items:center;justify-content:center}

/* Newsletter */
.news{left:111px;top:2490px;width:977px;height:398px;border-radius:16px;overflow:hidden}
.news-bg{left:0;top:0;width:977px;height:398px;background:linear-gradient(90deg,#3d3350 0%,#7a5a7a 30%,#2e4a80 60%,#274a85 100%)}
.news-title{left:442px;top:50px;font-family:"Quicksand",sans-serif;font-weight:700;font-size:43px;color:var(--white);display:flex;align-items:center;gap:14px}
.news-title .mark{border-color:var(--white);width:32px;height:32px}
.news-sub{left:446px;top:115px;font-size:14.5px;color:var(--white)}
.field{background:var(--white);border-radius:4px;height:45px;display:flex;align-items:center;padding-left:15px;font-size:12.5px;color:#777}
.btn-sub{left:447px;top:277px;width:105px;height:38px}
.news-note{left:476px;top:334px;font-style:italic;font-size:12px;letter-spacing:.8px;color:var(--white)}

/* Mission */
.mission-title{left:107px;top:3002px;font-size:41px}
.mission-text{left:110px;top:3066px;width:440px;font-size:16px;line-height:28.5px;color:var(--muted)}
.mission-text p{margin-bottom:11px}
.mission-img{top:3002px;width:239px;height:223px;border-radius:4px}

/* Footer */
.footer-wave{left:0;top:3300px;width:1200px;height:120px}
.footer{left:0;top:3415px;width:1200px;height:367px;background:var(--footer);color:var(--white)}
.foot-brand{left:117px;top:80px;display:flex;align-items:center;gap:20px;font-family:"Quicksand",sans-serif;font-weight:700;font-size:52px;line-height:54px;color:var(--teal)}
.foot-brand .brand-dot{width:40px;height:40px}
.social{left:108px;top:262px;display:flex;gap:6px}
.social span{width:30px;height:30px;border-radius:50%;background:var(--white)}
.social span:first-child{background:var(--teal)}
.foot-h{font-family:"Open Sans",sans-serif;font-weight:700;font-size:14.5px;letter-spacing:.5px}
.foot-links{left:582px;top:80px}
.foot-links ul{list-style:none;margin-top:16px;font-size:13px;line-height:32px}
.foot-contact{left:803px;top:80px;width:300px}
.contact-row{display:flex;gap:14px;font-size:13px;line-height:22px;margin-top:14px}
.contact-row svg{width:22px;height:22px;flex:none}
.foot-rule{left:108px;top:312px;width:979px;height:1px;background:#555}
.copy{left:0;top:330px;width:1200px;text-align:center;font-family:"Open Sans",sans-serif;font-size:13.5px;letter-spacing:1.2px}
</style>
</head>
<body>

<header>
  <div class="abs topbar">
    <span><svg viewBox="0 0 24 24" fill="#fff"><path d="M12 2a7 7 0 0 0-7 7c0 5 7 13 7 13s7-8 7-13a7 7 0 0 0-7-7zm0 9.5A2.5 2.5 0 1 1 12 6.5a2.5 2.5 0 0 1 0 5z"/></svg>Lorem Ipsum,USA -437916</span>
    <span><svg viewBox="0 0 24 24"><circle cx="12" cy="12" r="11" fill="#fff"/><path d="M8.5 6.5l2 2.5-1.2 1.5a8 8 0 0 0 4 4l1.5-1.2 2.5 2-1 2c-4.5.3-9.3-4.5-9-9z" fill="#17793a"/></svg>(555) 218-0147</span>
    <span><svg viewBox="0 0 24 24"><circle cx="12" cy="12" r="11" fill="#fff"/><rect x="6.5" y="8" width="11" height="8" rx="1" fill="#17793a"/><path d="M6.5 8.5l5.5 4 5.5-4" stroke="#fff" fill="none"/></svg>hello@mendedlovedwhole.org</span>
  </div>
  <a class="abs brand" href="#"><span class="brand-dot"></span><span class="brand-name">Mended Loved Whole</span></a>
  <nav class="abs nav">
    <a class="active" href="#">Home</a>
    <a href="#">About Us</a>
    <a href="#">Meetings &amp; Events</a>
    <a href="#">Lanterns by the River</a>
    <a href="#">Healing Rooms</a>
    <a href="#">Live Stream</a>
  </nav>
  <a class="abs btn-contact" href="#">Contact Us</a>
</header>

<section>
  <div class="abs hero" role="img" aria-label="Congregation worshipping with raised hands in a church sanctuary with a cross on the front wall"></div>
  <h1 class="abs hero-title">Mended, Loved, Whole</h1>
  <p class="abs hero-sub">Gather with us for worship, healing encounters, and life-changing community.</p>
  <a class="abs btn hero-btn" href="#">Join Us</a>
  <svg class="abs hero-wave" viewBox="0 0 1200 115" preserveAspectRatio="none">
    <path d="M0 75 C250 -10 480 10 720 55 C900 90 1080 80 1200 10 L1200 115 L0 115Z" fill="#0aa394"/>
    <path d="M0 90 C250 10 480 30 720 75 C900 108 1080 95 1200 28 L1200 115 L0 115Z" fill="#fff"/>
  </svg>
</section>

<section>
  <div class="abs who-photo" role="img" aria-label="Ministry founders, a married couple, standing before a stained glass window"></div>
  <h2 class="abs section-title who-title"><span class="mark"></span>Who <b>We Are</b></h2>
  <div class="abs who-text">
    <p>Daniel and Ruth Ellen have been married for 42 years and have two adult children. They both grew up in southern Illinois.</p>
    <p>Their desire is to share the love of Christ with others. They have numerous stories to share about the many ways they have seen God move in their lives as well as the lives of others.</p>
    <p>They believe in the manifestation of God's power through signs and wonders. They have not only witnessed God's power through signs and wonders them they have also experienced His miraculous healing touch personally.</p>
  </div>
  <a class="abs btn who-btn" href="#">Read More</a>
</section>

<section>
  <div class="abs book-band" role="img" aria-label="Dimmed background of a worship gathering"></div>
  <h2 class="abs book-title"><span class="mark"></span>Lanterns by the River</h2>
  <p class="abs book-text">The book is a six-week guided journal with a short daily devotion. The first week examines the "I am" statements of Jesus found in the Gospel of John. The following five weeks will focus on Scriptures and identify "I am" statements that will unveil who you are in the eyes of God.</p>
  <a class="abs btn book-btn" href="#">Buy Now</a>
  <div class="abs book-cover" role="img" aria-label="Book cover for the guided journal by Ruth Ellen Carver showing yellow flowers in rain"></div>
</section>

<section>
  <h2 class="abs section-title blog-title"><span class="mark"></span>Our <b>Blog</b></h2>
  <span class="abs arrow" style="left:29px;background:var(--teal)"><svg width="10" height="10" viewBox="0 0 10 10"><path d="M6.5 1.5L3 5l3.5 3.5" stroke="#fff" stroke-width="2" fill="none"/></svg></span>
  <span class="abs arrow" style="left:1125px;background:#bbb"><svg width="10" height="10" viewBox="0 0 10 10"><path d="M3.5 1.5L7 5 3.5 8.5" stroke="#fff" stroke-width="2" fill="none"/></svg></span>
  <article class="abs card" style="left:107px">
    <div class="card-img" role="img" aria-label="Rainbow arching over a straight country road" style="background:linear-gradient(180deg,#a9b6c6,#c8cdb8 60%,#7a8a5a)"></div>
    <p class="card-cat">News</p>
    <h3 class="card-h" style="font-weight:400">Healing amidst the car accident</h3>
    <div class="card-meta"><span><i></i>May 6, 2020</span><span><i></i>4 Comments</span></div>
  </article>
  <article class="abs card" style="left:439px">
    <div class="card-img" role="img" aria-label="Eagle flying against a golden sunset between trees" style="background:linear-gradient(180deg,#e8a33a,#f3c25a 50%,#5a3a18)"></div>
    <p class="card-cat">News</p>
    <h3 class="card-h" style="font-weight:400;margin-top:12px">Healing – where and how can it happen?</h3>
    <div class="card-meta" style="margin-top:14px"><span><i></i>May 6, 2020</span><span><i></i>4 Comments</span></div>
  </article>
  <article class="abs card" style="left:770px">
    <div class="card-img" role="img" aria-label="Open hands beneath a cloud of faith words" style="background:linear-gradient(180deg,#3b3f5a,#5a5f7a 60%,#2a2d40)"></div>
    <p class="card-cat">News</p>
    <h3 class="card-h" style="font-weight:400">Why is healing important?</h3>
    <div class="card-meta"><span><i></i>April 17, 2020</span><span><i></i>4 Comments</span></div>
  </article>
</section>

<section class="abs news">
  <div class="abs news-bg" role="img" aria-label="Wooden cross on a hill against a colourful sunset sky"></div>
  <h2 class="abs news-title"><span class="mark"></span>Join Our Newsletter</h2>
  <p class="abs news-sub">Signup today for free and be the first to get notified on new updates.</p>
  <div class="abs field" style="left:446px;top:160px;width:238px">Foirst Name</div>
  <div class="abs field" style="left:695px;top:160px;width:239px">Last Name</div>
  <div class="abs field" style="left:446px;top:214px;width:488px">Enter Email Address</div>
  <a class="abs btn btn-sub" href="#">Subscribe</a>
  <p class="abs news-note">And don't worry, we hate spam too! You can unsubscribe at anytime.</p>
</section>

<section>
  <h2 class="abs section-title mission-title"><span class="mark"></span>Our <b>Mission &amp; Vision</b></h2>
  <div class="abs mission-text">
    <p>Honoring God's presence by loving the broken, saving the lost, and healing the</p>
    <p>Mended, Loved, Whole is here to activate, proclaim and teach the love of the Father through Jesus with the guidance of the Holy Spirit</p>
  </div>
  <div class="abs mission-img" style="left:600px;background:linear-gradient(180deg,#8a6f5a,#5a4a40 60%,#3a2e28)" role="img" aria-label="Worship team leading a song at the front of the church"></div>
  <div class="abs mission-img" style="left:848px;background:linear-gradient(180deg,#b9a888,#6a5a48 60%,#3a3028)" role="img" aria-label="People kneeling in prayer during a gathering"></div>
</section>

<footer>
  <svg class="abs footer-wave" viewBox="0 0 1200 120" preserveAspectRatio="none">
    <path d="M0 95 C200 30 420 15 650 45 C850 70 1050 70 1200 20 L1200 120 L0 120Z" fill="#0aa394"/>
    <path d="M0 110 C200 50 420 40 650 68 C850 92 1050 90 1200 40 L1200 120 L0 120Z" fill="#0b0b0b"/>
  </svg>
  <div class="abs footer">
    <a class="abs foot-brand" href="#"><span class="brand-dot"></span><span style="width:200px">Mended Loved Whole</span></a>
    <div class="abs social" aria-label="Social links"><span></span><span></span><span></span><span></span></div>
    <div class="abs foot-links">
      <h4 class="foot-h">QUICK LINKS</h4>
      <ul><li>Home</li><li>About Us</li><li>Meetings &amp; Events</li><li>Lanterns by the River</li><li>Healing Rooms</li><li>Live Stream</li></ul>
    </div>
    <div class="abs foot-contact">
      <h4 class="foot-h">CONTACT INFO</h4>
      <div class="contact-row" style="margin-top:20px"><svg viewBox="0 0 24 24"><circle cx="12" cy="12" r="11" fill="#fff"/><path d="M12 5a4.5 4.5 0 0 0-4.5 4.5c0 3.3 4.5 8.5 4.5 8.5s4.5-5.2 4.5-8.5A4.5 4.5 0 0 0 12 5zm0 6a1.5 1.5 0 1 1 0-3 1.5 1.5 0 0 1 0 3z" fill="#0b0b0b"/></svg><span>412 Cedar Hollow Lane, Fairbrook, IL, United States, 60019</span></div>
      <div class="contact-row" style="margin-top:20px"><svg viewBox="0 0 24 24"><circle cx="12" cy="12" r="11" fill="#fff"/><path d="M8.5 6.5l2 2.5-1.2 1.5a8 8 0 0 0 4 4l1.5-1.2 2.5 2-1 2c-4.5.3-9.3-4.5-9-9z" fill="#0b0b0b"/></svg><span>(555) 218-0147</span></div>
      <div class="contact-row" style="margin-top:22px"><svg viewBox="0 0 24 24"><circle cx="12" cy="12" r="11" fill="#fff"/><rect x="6.5" y="8" width="11" height="8" rx="1" fill="#0b0b0b"/><path d="M6.5 8.5l5.5 4 5.5-4" stroke="#fff" fill="none"/></svg><span>hello@mendedlovedwhole.org</span></div>
    </div>
    <div class="abs foot-rule"></div>
    <p class="abs copy">© 2025 Mended Loved Whole .All Rights Reserved</p>
  </div>
</footer>

</body>
</html>
```